Varelko App for Smart Devices IoT WiFi Electronic

Varelko is a siren manufacturer. This application is used for the company's products that have a Wi-Fi connection and an internet connection, which can be configured and activated remotely through this application. In addition, this application is used to activate the siren at specific times for the start and end of shifts in companies and schools. Users will be siren installers and IT or HR managers.
In addition to activating motorized sirens timers, some siren models have speakers and allow you to play TTS (text to speech) audio, audio recorded by the user on the phone and upload audio (mp3) with playlist programming with start and end times.
Application screens: home with dashboard (one dashboard for each category). Device categories: timers, speakers, motorized siren. Screen for requesting evaluation in the Play Store. Screen for registering the user profile. Screen for registering devices according to their category (timers, speakers, motorized siren). Screen for registering device groups. Screen for pairing the device on the client's Wi-Fi network. Screen for registering activation times. Screen for uploading MP3 audios. Screen for registering playlists with audio selection, start and end times. Screen for recording audio for later sending to the speakers. Screen for converting text to speech and sending to the speakers. It is important to have a time picker with the day of the week to program the activation times and playlist.

Target Market(s)

Schools, Companies and Stores.

Industry/Entity Type

IoT

Font styles to use
Sans Serif
Other font styles liked:
• roboto

Colors
FFC000
F8CF3A
FAE287
FDF2CF
FEFAEE

Requirements
Must have
• time picker with weekdays for timer programming feature.
Nice to have
• app review request screen on play store

```html
<!DOCTYPE html>
<html lang="en">
<head>
<meta charset="UTF-8">
<title>Varelko – Log In</title>
<link href="https://fonts.googleapis.com/css2?family=Roboto:wght@400;500;700&display=swap" rel="stylesheet">
<style>
  :root {
    --amber: #FFC000;
    --amber-button: #F2BE00;
    --gold: #F8CF3A;
    --sand: #FAE287;
    --cream: #FDF2CF;
    --ivory: #FEFAEE;
    --ink: #1E1E1E;
    --ink-soft: #3A3A3A;
    --muted: #5E5E5E;
    --field-border: #ECECEC;
    --link-blue: #3B7BF0;
    --white: #FFFFFF;
  }
  * { box-sizing: border-box; margin: 0; padding: 0; }
  html, body {
    width: 1200px;
    height: 2181px;
    overflow: hidden;
    font-family: "Roboto", sans-serif;
    background: var(--white);
  }
  .screen {
    position: relative;
    width: 1200px;
    height: 2181px;
    overflow: hidden;
    background: linear-gradient(180deg, #F1D58F 0%, #F6D77A 35%, var(--gold) 62%, #F9D44C 100%);
  }
  .status-bar {
    position: absolute;
    top: 0; left: 0; right: 0;
    height: 120px;
    display: flex;
    align-items: center;
    justify-content: space-between;
    padding: 0 70px 0 64px;
  }
  .status-time { font-size: 40px; font-weight: 700; color: var(--ink); }
  .status-icons { display: flex; gap: 18px; align-items: center; }
  .brand {
    position: absolute;
    top: 740px;
    left: 0; right: 0;
    text-align: center;
    font-size: 200px;
    font-weight: 500;
    letter-spacing: -4px;
    color: var(--ivory);
    line-height: 1;
  }
  .hero-title {
    position: absolute;
    top: 990px;
    left: 0; right: 0;
    text-align: center;
    font-size: 84px;
    font-weight: 700;
    letter-spacing: -2px;
    color: var(--ink);
  }
  .hero-subtitle {
    position: absolute;
    top: 1096px;
    left: 0; right: 0;
    text-align: center;
    font-size: 33px;
    color: var(--ink-soft);
  }
  .login-sheet {
    position: absolute;
    top: 1221px;
    left: 0; right: 0; bottom: 0;
    background: var(--white);
    border-radius: 128px 128px 0 0;
    padding: 118px 67px 0;
  }
  .field-label {
    display: block;
    font-size: 32px;
    color: var(--muted);
    margin-bottom: 22px;
  }
  .field {
    height: 106px;
    border: 3px solid var(--field-border);
    border-radius: 30px;
    display: flex;
    align-items: center;
    justify-content: space-between;
    padding: 0 40px;
    font-size: 37px;
    font-weight: 500;
    color: var(--ink);
  }
  .field + .field-label { margin-top: 62px; }
  .field-password { letter-spacing: 4px; }
  .options-row {
    margin-top: 48px;
    display: flex;
    justify-content: space-between;
    align-items: center;
    font-size: 32px;
  }
  .remember { display: flex; align-items: center; gap: 26px; color: var(--muted); }
  .checkbox {
    width: 34px; height: 34px;
    border: 3px solid #6E6E6E;
    border-radius: 6px;
  }
  .forgot-link { color: var(--link-blue); font-weight: 500; }
  .login-button {
    margin-top: 100px;
    height: 110px;
    border-radius: 24px;
    background: var(--amber-button);
    display: flex;
    align-items: center;
    justify-content: center;
    font-size: 38px;
    font-weight: 500;
    color: var(--ivory);
  }
  .signup-row {
    margin-top: 62px;
    text-align: center;
    font-size: 31px;
    color: var(--muted);
  }
  .signup-link { color: var(--amber); font-weight: 500; margin-left: 18px; }
</style>
</head>
<body>
  <main class="screen">
    <div class="status-bar">
      <span class="status-time">09:41</span>
      <span class="status-icons">
        <svg width="40" height="26" viewBox="0 0 40 26" aria-hidden="true">
          <rect x="0" y="18" width="7" height="8" rx="1.5" fill="#1E1E1E"/>
          <rect x="11" y="13" width="7" height="13" rx="1.5" fill="#1E1E1E"/>
          <rect x="22" y="7" width="7" height="19" rx="1.5" fill="#1E1E1E"/>
          <rect x="33" y="1" width="7" height="25" rx="1.5" fill="#1E1E1E" opacity="0.35"/>
        </svg>
        <svg width="38" height="28" viewBox="0 0 38 28" aria-hidden="true">
          <path d="M19 26 L13 19 A9 9 0 0 1 25 19 Z" fill="#1E1E1E"/>
          <path d="M7 13 A17 17 0 0 1 31 13" stroke="#1E1E1E" stroke-width="4.5" fill="none" stroke-linecap="round"/>
          <path d="M2 7 A25 25 0 0 1 36 7" stroke="#1E1E1E" stroke-width="4.5" fill="none" stroke-linecap="round"/>
        </svg>
        <svg width="62" height="28" viewBox="0 0 62 28" aria-hidden="true">
          <rect x="1.5" y="1.5" width="53" height="25" rx="7" fill="none" stroke="#1E1E1E" stroke-width="3" opacity="0.4"/>
          <rect x="5" y="5" width="46" height="18" rx="4" fill="#1E1E1E"/>
          <rect x="57" y="9" width="4" height="10" rx="2" fill="#1E1E1E" opacity="0.4"/>
        </svg>
      </span>
    </div>

    <div class="brand">Varelko</div>
    <h1 class="hero-title">Get Started now</h1>
    <p class="hero-subtitle">Create an account or log in to explore about our app</p>

    <section class="login-sheet">
      <label class="field-label">User Name / Email</label>
      <div class="field">Enter User Name</div>

      <label class="field-label">Password</label>
      <div class="field field-password">
        <span>*******</span>
        <svg width="40" height="40" viewBox="0 0 24 24" aria-hidden="true" fill="none" stroke="#9A9A9A" stroke-width="1.6" stroke-linecap="round">
          <path d="M2 12s3.5-6 10-6 10 6 10 6-3.5 6-10 6S2 12 2 12z"/>
          <circle cx="12" cy="12" r="3"/>
          <path d="M4 4l16 16"/>
        </svg>
      </div>

      <div class="options-row">
        <span class="remember"><span class="checkbox"></span>Remember me</span>
        <span class="forgot-link">Forgot Password ?</span>
      </div>

      <div class="login-button">Log In</div>

      <p class="signup-row">Don't have an account?<span class="signup-link">Sign Up</span></p>
    </section>
  </main>
</body>
</html>
```